Marlow Estate Fixers (Handyman / Home Improvement Company)

Looking for a double sided professional looking business card with Logo attached to be highlighted on one side and throwing in an image of a handyman as an option would be nice to see as well. We are a company focused on providing quality Handyman and Home improvement services in a timely manner that is done right the first time with integrity

Industry/Entity Type

Handyman / Home Improvement

Contact Information for Business Card

(LOGO, Name, Mobile and office phone numbers, email) on front side of card, (the words "The SOLUTION to all of your Handyman and Home Improvement needs" followed by "Family Owned and Operated" at the very bottom) on the back.

Colors
EB3D1F
EC4F4E
F09395
F8D3D4
FCEDEE

Requirements
Must have
• Red, Gray, Black Color scheme
Should not have
• No Yellow or Blue colors

```html
<!DOCTYPE html>
<html lang="en">
<head>
<meta charset="UTF-8">
<title>Marlow Estate Fixers – Business Card</title>
<link href="https://fonts.googleapis.com/css2?family=Montserrat:wght@400;500;700;800&display=swap" rel="stylesheet">
<style>
  :root {
    --backdrop: #9a9a9a;
    --card: #151515;
    --red: #e5262b;
    --white: #ffffff;
    --soft-white: #f2f2f2;
  }
  * { margin: 0; padding: 0; box-sizing: border-box; }
  html, body {
    width: 1200px;
    height: 1108px;
    overflow: hidden;
    background: var(--backdrop);
    font-family: "Montserrat", Arial, sans-serif;
  }
  .card {
    position: absolute;
    left: 242px;
    width: 715px;
    height: 409px;
    border-radius: 36px;
    background: var(--card);
    color: var(--white);
  }
  .card--back { top: 119px; }
  .card--front { top: 580px; }

  .tagline {
    position: absolute;
    top: 29px;
    left: 0;
    width: 100%;
    text-align: center;
    font-size: 17.5px;
    font-weight: 700;
    letter-spacing: 0.1px;
  }
  .footer-line {
    position: absolute;
    top: 361px;
    left: 0;
    width: 100%;
    text-align: center;
    font-size: 17px;
    font-weight: 500;
    letter-spacing: 0.6px;
    color: var(--soft-white);
  }

  .brand {
    position: absolute;
    display: flex;
    flex-direction: column;
    align-items: center;
    text-align: center;
    color: var(--white);
    font-weight: 800;
    text-transform: uppercase;
    line-height: 1.05;
  }
  .brand__dot {
    border-radius: 50%;
    background: var(--red);
  }
  .card--back .brand {
    left: 0; width: 100%; top: 118px;
  }
  .card--back .brand__dot { width: 46px; height: 46px; margin-bottom: 18px; }
  .card--back .brand__name { font-size: 38px; letter-spacing: 1px; }

  .card--front .brand {
    left: 20px; width: 300px; top: 133px;
  }
  .card--front .brand__dot { width: 36px; height: 36px; margin-bottom: 14px; }
  .card--front .brand__name { font-size: 28px; letter-spacing: 0.8px; }

  .divider {
    position: absolute;
    left: 325px;
    top: 82px;
    width: 2px;
    height: 244px;
    background: var(--red);
  }
  .contact {
    position: absolute;
    left: 351px;
    top: 76px;
  }
  .contact__name {
    font-size: 30px;
    font-weight: 700;
    color: var(--red);
    letter-spacing: 0.3px;
    line-height: 1.2;
  }
  .contact__role {
    margin-top: 4px;
    font-size: 17px;
    font-weight: 500;
    letter-spacing: 0.4px;
  }
  .contact__address {
    margin-top: 20px;
    font-size: 17px;
    font-weight: 500;
    line-height: 27px;
    letter-spacing: 0.4px;
  }
  .contact__list {
    list-style: none;
    margin-top: 13px;
  }
  .contact__item {
    display: flex;
    align-items: center;
    height: 27px;
    font-size: 17px;
    font-weight: 500;
    letter-spacing: 0.4px;
  }
  .contact__icon {
    width: 16px;
    height: 16px;
    margin-right: 9px;
    flex: none;
    fill: var(--red);
  }
</style>
</head>
<body>

<section class="card card--back" aria-label="Card back">
  <p class="tagline">Your SOLUTION to all of your Handyman and Home Improvement needs</p>
  <div class="brand">
    <span class="brand__dot"></span>
    <span class="brand__name">Marlow Estate<br>Fixers</span>
  </div>
  <p class="footer-line">Family Owned and Operated</p>
</section>

<section class="card card--front" aria-label="Card front">
  <div class="brand">
    <span class="brand__dot"></span>
    <span class="brand__name">Marlow Estate<br>Fixers</span>
  </div>
  <div class="divider"></div>
  <div class="contact">
    <h1 class="contact__name">DANIEL HARROW</h1>
    <p class="contact__role">Managing Director</p>
    <p class="contact__address">Your address, City<br>State, Zip 1234</p>
    <ul class="contact__list">
      <li class="contact__item">
        <svg class="contact__icon" viewBox="0 0 16 16" aria-hidden="true"><path d="M4 0h8a1.5 1.5 0 0 1 1.5 1.5v13A1.5 1.5 0 0 1 12 16H4a1.5 1.5 0 0 1-1.5-1.5v-13A1.5 1.5 0 0 1 4 0zm0.5 2v10.5h7V2zM8 13.3a0.9 0.9 0 1 0 0 1.8 0.9 0.9 0 0 0 0-1.8z"/></svg>
        123 456 789
      </li>
      <li class="contact__item">
        <svg class="contact__icon" viewBox="0 0 16 16" aria-hidden="true"><path d="M1 5.5C1 3.5 4.5 2 8 2s7 1.5 7 3.5V7h-3.5V5.5h-7V7H1zM4 8l1.5-2h5L12 8l2 6H2zm4 1.2a2 2 0 1 0 0 4 2 2 0 0 0 0-4z"/></svg>
        123 456 789
      </li>
      <li class="contact__item">
        <svg class="contact__icon" viewBox="0 0 16 16" aria-hidden="true"><path d="M1 3.5h14v9H1zm1.3 1.2L8 9l5.7-4.3z"/></svg>
        info@marlowestatefixers.com
      </li>
      <li class="contact__item">
        <svg class="contact__icon" viewBox="0 0 16 16" aria-hidden="true"><path d="M8 1a7 7 0 1 0 0 14A7 7 0 0 0 8 1zm0 1.5a5.5 5.5 0 0 1 1.6.2L8.5 4.5 6.5 4l-1 1.8 1.7 1.5-0.6 2.2 1.9 1.6-0.3 2.8A5.5 5.5 0 0 1 4 4.3l1.3 0.2z"/></svg>
        www.marlowestatefixers.com
      </li>
    </ul>
  </div>
</section>

</body>
</html>
```